Create a proposal + product powerpoint

Please see the powerpoint for the slides. There are about 20 slides to be created. Rest of them are for reference and show the design that I like.

I would like to move fast on this, since I need to present it next week (in the week of April 21st).

Please download the current content from here:
https://www.parcelbrook.net/fetch/qRtVmXzLwPkNbYcD

Please make at least 4 slides with the specific content so I can assess your design style.

Target Market(s)

Business Audience and very senior technical audience
Decision Makers

Industry/Entity Type

Product

Colors
e34297
a64599

Requirements
Must have
• Should be very clean, crisp.

I like to use Icons as shown in the powerpoint.... Please see the appendix of the slide deck that shows the various icons. Most of them just have plain text, and I would like to organize so that it does not look like some is just reading text.

I would like to focus on the design aspects so that the audience is clear on how the solution works.

Every page should some graphic element based on the slides shown in the appendix.

```html
<!DOCTYPE html>
<html lang="en">
<head>
<meta charset="utf-8">
<title>Project Plan</title>
<link rel="stylesheet" href="https://fonts.googleapis.com/css2?family=Roboto+Condensed:wght@400;700&family=Josefin+Sans:wght@400&display=swap">
<style>
  :root {
    --title-purple: #9a1fa8;
    --label-purple: #7a2a80;
    --bar: #ae73b3;
    --note: #8e3a8e;
    --axis: #8a5a9a;
    --grid: #efe4f0;
    --milestone: #9e4f9e;
    --footer-dark: #9b1f5e;
    --footer-light: #b04aa8;
    --rule: #dcdcdc;
    --logo-grey: #8c8c8c;
    --white: #ffffff;
  }
  html, body { margin: 0; padding: 0; overflow: hidden; }
  body { width: 1200px; height: 900px; background: var(--white); }
  .slide {
    position: relative; width: 1200px; height: 900px; overflow: hidden;
    background: var(--white);
    font-family: "Roboto Condensed", Arial, sans-serif;
  }
  .slide-decoration {
    position: absolute; left: 900px; top: 93px; width: 300px; height: 749px;
    background: linear-gradient(100deg, rgba(255,255,255,0) 0%, rgba(220,150,225,0.55) 45%, #c456d4 100%);
  }
  .slide-haze {
    position: absolute; left: 0; top: 500px; width: 260px; height: 340px;
    background: radial-gradient(circle at 0% 60%, rgba(200,120,210,0.25), rgba(255,255,255,0) 70%);
  }
  .slide-title {
    position: absolute; left: 40px; top: 20px; margin: 0;
    font-size: 42px; font-weight: 400; color: var(--title-purple);
  }
  .logo-box {
    position: absolute; left: 1035px; top: 12px; width: 150px; height: 66px;
    box-sizing: border-box; border: 2px solid #e6e6e6; border-radius: 8px;
    display: flex; align-items: center; justify-content: center;
    font-size: 28px; color: var(--logo-grey); letter-spacing: 1px; background: var(--white);
  }
  .header-rule {
    position: absolute; left: 40px; top: 90px; width: 1145px; height: 2px; background: var(--rule);
  }
  .chart { position: absolute; left: 0; top: 0; }
  .chart-axis-label { font-family: "Josefin Sans", Arial, sans-serif; font-size: 18px; fill: #5a2a60; }
  .chart-week { font-family: "Josefin Sans", Arial, sans-serif; font-size: 20px; fill: #6a2a70; }
  .chart-note { font-family: "Josefin Sans", Arial, sans-serif; font-size: 14px; fill: var(--note); }
  .chart-bar { fill: var(--bar); }
  .milestones {
    position: absolute; left: 57px; top: 730px; height: 82px;
    display: flex; align-items: center;
  }
  .milestones-label { font-size: 31px; color: var(--label-purple); width: 158px; }
  .milestone {
    width: 228px; height: 82px; margin-right: 6px; background: var(--milestone);
    border-radius: 4px; color: var(--white); text-align: center;
    display: flex; flex-direction: column; justify-content: center; line-height: 1.05;
  }
  .milestone-phase { font-size: 30px; font-weight: 700; }
  .milestone-phase sup { font-size: 17px; }
  .milestone-time { font-size: 26px; }
  .milestone-time b { font-size: 32px; }
  .footer { position: absolute; left: 0; top: 842px; }
  .footer-text { font-size: 22px; fill: var(--white); font-family: "Roboto Condensed", Arial, sans-serif; }
</style>
</head>
<body>
<main class="slide">
  <div class="slide-haze" aria-hidden="true"></div>
  <div class="slide-decoration" role="img" aria-label="Decorative pattern of pink and purple triangles"></div>

  <h1 class="slide-title">Project Plan</h1>
  <div class="logo-box">LOGO HERE</div>
  <div class="header-rule"></div>

  <svg class="chart" width="1200" height="900" viewBox="0 0 1200 900" aria-label="Weekly volume chart, weeks 1 to 14">
    <g stroke="var(--grid)" stroke-width="1">
      <line x1="145" y1="173" x2="982" y2="173"/>
      <line x1="145" y1="249" x2="982" y2="249"/>
      <line x1="145" y1="324" x2="982" y2="324"/>
      <line x1="145" y1="400" x2="982" y2="400"/>
      <line x1="145" y1="475" x2="982" y2="475"/>
      <line x1="145" y1="551" x2="982" y2="551"/>
    </g>
    <g class="chart-axis-label" text-anchor="end">
      <text x="130" y="179">6,000</text>
      <text x="130" y="255">5,000</text>
      <text x="130" y="330">4,000</text>
      <text x="130" y="406">3,000</text>
      <text x="130" y="481">2,000</text>
      <text x="130" y="557">1,000</text>
      <text x="130" y="632">0</text>
    </g>
    <g class="chart-bar">
      <rect x="155" y="584" width="50" height="42"/>
      <rect x="215" y="496" width="50" height="130"/>
      <rect x="275" y="507" width="50" height="119"/>
      <rect x="335" y="203" width="50" height="423"/>
      <rect x="395" y="300" width="50" height="326"/>
      <rect x="455" y="390" width="50" height="236"/>
      <rect x="515" y="385" width="50" height="241"/>
      <rect x="575" y="495" width="50" height="131"/>
      <rect x="635" y="523" width="50" height="103"/>
      <rect x="695" y="419" width="50" height="207"/>
      <rect x="755" y="500" width="50" height="126"/>
      <rect x="815" y="542" width="50" height="84"/>
      <rect x="875" y="554" width="50" height="72"/>
      <rect x="935" y="515" width="50" height="111"/>
    </g>
    <line x1="145" y1="626" x2="985" y2="626" stroke="var(--axis)" stroke-width="2"/>
    <g class="chart-week" text-anchor="middle">
      <text x="180" y="656">W1</text><text x="240" y="656">W2</text><text x="300" y="656">W3</text>
      <text x="360" y="656">W4</text><text x="420" y="656">W5</text><text x="480" y="656">W6</text>
      <text x="540" y="656">W7</text><text x="600" y="656">W8</text><text x="660" y="656">W9</text>
      <text x="720" y="656">W10</text><text x="780" y="656">W11</text><text x="840" y="656">W12</text>
      <text x="900" y="656">W13</text><text x="960" y="656">W14</text>
    </g>
    <g class="chart-note">
      <text x="392" y="216">First week of full product range.</text>
      <text x="392" y="235">Leafies kick-in</text>
      <text x="638" y="511">Xmas</text>
      <text x="750" y="431">Advertising kick-in</text>
    </g>
  </svg>

  <section class="milestones">
    <div class="milestones-label">Milestones:</div>
    <div class="milestone"><span class="milestone-phase">1<sup>st</sup> Phase</span><span class="milestone-time">After <b>3</b> months</span></div>
    <div class="milestone"><span class="milestone-phase">2<sup>nd</sup> Phase</span><span class="milestone-time">After <b>5</b> months</span></div>
    <div class="milestone"><span class="milestone-phase">3<sup>rd</sup> Phase</span><span class="milestone-time">After <b>7</b> months</span></div>
  </section>

  <svg class="footer" width="1200" height="58" viewBox="0 842 1200 58">
    <polygon points="0,842 907,842 937,900 0,900" fill="var(--footer-dark)"/>
    <polygon points="922,842 1200,842 1200,900 952,900" fill="var(--footer-light)"/>
    <text class="footer-text" x="14" y="879">Page : 01</text>
    <text class="footer-text" x="1186" y="879" text-anchor="end">Copyright text here</text>
  </svg>
</main>
</body>
</html>
```